Business Card Design

We like to use greens as you will see in our logo (but not TOO much green). We are a Dental Clinic in a somewhat eccentric community. We do not like the dated sharp designs which we see many dentists use. We're looking for something bright and fresh while still maintaining the integrity of the profession. Elegance is not necessarily what we are going for... we need for the design to be "mature" but also up-lifting.

See our logo.
Updates

Project Deadline Extended
Reason: We have 5 designs which we like. But we'd like to see a few more before committing to a design.

Project Deadline Extended
Reason: We are awaiting revisions to this project. We are still welcoming designs while we wait to see if designers are able to provide to us the revisions we require in order to proceed with a selection.

Target Market(s)

Younger families - ages late 20's to early 40's

Industry/Entity Type

Business

Contact Information for Business Card

Corwel T. Banfry DDS 2730 W. Halvert Rd. Ste. 7 Royal Oak, MI 48391 (248)555-0174 FX (248)555-0189 info@BrightwellDentalCareMi.com BrigthwellDentalCareMi.com on the back of the card we need an appointment reminder (For____ Date___ Time____) with "If you are unable to keep your appointment, kindly give 48 hours notice" at the bottom. No use of teeth in the design. DOUBLE SIDED DESIGN

Requirements
Should not have
• The use of pictures of teeth

```html
<!DOCTYPE html>
<html lang="en">
<head>
<meta charset="utf-8">
<title>Brightwell Dental Care – Business Card</title>
<link href="https://fonts.googleapis.com/css2?family=Open+Sans:ital,wght@0,400;0,600;0,700;1,400;1,600&family=Cinzel:wght@500&display=swap" rel="stylesheet">
<style>
  :root {
    --green-dark: #1d6b34;
    --green-mid: #2a8a3a;
    --green-light: #3aa640;
    --ink: #2b2b2b;
    --card-edge: #3a3a3a;
    --paper: #ffffff;
    --backdrop: #ececec;
  }
  html, body {
    margin: 0;
    padding: 0;
    width: 1200px;
    height: 1045px;
    overflow: hidden;
    background: var(--backdrop);
    font-family: "Open Sans", Arial, sans-serif;
    color: var(--ink);
  }
  .canvas { position: relative; width: 1200px; height: 1045px; }
  .card {
    position: absolute;
    background: var(--paper);
    border: 1.5px solid var(--card-edge);
    border-radius: 30px;
    overflow: hidden;
    box-sizing: border-box;
  }

  /* ---------- front ---------- */
  .card-front { left: 341px; top: 47px; width: 812px; height: 464px; }
  .brand {
    position: absolute;
    display: flex;
    align-items: center;
    gap: 14px;
  }
  .brand-dot {
    border-radius: 50%;
    background: var(--green-light);
    flex: none;
  }
  .brand-name {
    color: var(--green-dark);
    font-weight: 600;
    line-height: 1;
    text-align: center;
  }
  .brand-name .word { display: block; }
  .brand-name .sub { display: block; letter-spacing: 0.04em; margin-top: 8px; }

  .card-front .brand { left: 52px; top: 66px; }
  .card-front .brand-dot { width: 34px; height: 34px; }
  .card-front .brand-name .word { font-size: 60px; }
  .card-front .brand-name .sub { font-size: 31px; }

  .rule { position: absolute; height: 2px; background: var(--green-dark); top: 173px; }
  .rule-left { left: 0; width: 28px; }
  .rule-right { left: 436px; right: 0; }

  .person { position: absolute; right: 20px; text-align: right; }
  .person-name { top: 131px; font-size: 26px; font-weight: 700; color: var(--green-dark); line-height: 36px; }
  .person-title { top: 182px; font-size: 19px; line-height: 26px; }

  .contacts {
    position: absolute;
    right: 20px;
    top: 256px;
    margin: 0; padding: 0;
    list-style: none;
    text-align: right;
    font-size: 19px;
    line-height: 33px;
  }
  .contacts li { display: flex; justify-content: flex-end; align-items: center; gap: 6px; }
  .contacts svg { width: 16px; height: 16px; fill: var(--green-dark); flex: none; }
  .address { position: absolute; right: 20px; top: 419px; font-size: 19px; line-height: 30px; }

  /* ---------- back ---------- */
  .card-back { left: 27px; top: 535px; width: 814px; height: 466px; }
  .appt-title {
    position: absolute; left: 64px; top: 89px;
    font-family: "Cinzel", Georgia, serif;
    font-weight: 500; font-size: 29px; letter-spacing: 0.03em;
    color: var(--green-dark); margin: 0;
  }
  .card-back .brand { left: 560px; top: 28px; }
  .card-back .brand-dot { width: 22px; height: 22px; }
  .card-back .brand-name .word { font-size: 40px; }
  .card-back .brand-name .sub { font-size: 21px; margin-top: 6px; }

  .field { position: absolute; font-size: 21px; line-height: 30px; }
  .dots { position: absolute; border-bottom: 2px dotted #777; height: 0; }
  .label-name { left: 70px; top: 159px; }
  .dots-name { left: 165px; width: 590px; top: 179px; }
  .label-date { left: 70px; top: 216px; }
  .dots-date { left: 165px; width: 228px; top: 236px; }
  .label-time { left: 400px; top: 216px; }
  .dots-time { left: 446px; width: 214px; top: 236px; }
  .label-ampm { left: 667px; top: 216px; }
  .label-next { left: 70px; top: 275px; }

  .slot {
    position: absolute; top: 273px; height: 31px;
    border: 1.5px solid #555; border-radius: 4px; box-sizing: border-box; background: var(--paper);
  }
  .slot-1 { left: 293px; width: 147px; }
  .slot-2 { left: 451px; width: 151px; }
  .slot-3 { left: 607px; width: 148px; }

  .days { position: absolute; left: 0; right: 0; top: 323px; height: 65px; }
  .days-week { position: absolute; left: 0; top: 0; width: 645px; height: 100%; background: var(--green-dark); }
  .days-sat { position: absolute; left: 649px; right: 0; top: 0; height: 100%; background: var(--green-light); }
  .day {
    position: absolute; top: 0; line-height: 65px;
    color: var(--paper); font-weight: 700; font-size: 22px;
  }
  .day-box {
    position: absolute; top: 18px; height: 29px;
    background: var(--paper); border: 1.5px solid #444; border-radius: 4px; box-sizing: border-box;
  }
  .notice {
    position: absolute; left: 64px; top: 407px;
    font-style: italic; font-size: 20.5px; line-height: 30px; margin: 0;
  }
</style>
</head>
<body>
<div class="canvas">

  <!-- Front of card -->
  <section class="card card-front" aria-label="Business card front">
    <div class="brand">
      <span class="brand-dot"></span>
      <span class="brand-name"><span class="word">Brightwell</span><span class="sub">DENTAL CARE</span></span>
    </div>
    <div class="rule rule-left"></div>
    <div class="rule rule-right"></div>

    <div class="person person-name">Corwel T. Banfry</div>
    <div class="person person-title">DDS</div>

    <ul class="contacts">
      <li>
        <svg viewBox="0 0 16 16" aria-hidden="true"><path d="M3.5 1.5l2.5 0 1 3.5-1.7 1.2c.8 1.8 2.2 3.2 4 4l1.2-1.7 3.5 1v2.5c0 .8-.7 1.5-1.5 1.5C7 13.5 2.5 9 2 3c0-.8.7-1.5 1.5-1.5z"/></svg>
        (248)555-0174
      </li>
      <li>
        <svg viewBox="0 0 16 16" aria-hidden="true"><path d="M2 8l1.5-4h9L14 8v4h-1.5v1.5h-2V12h-5v1.5h-2V12H2z M4 7h8l-1-2H5z M4 10a1 1 0 100-.01z"/></svg>
        (248)555-0189
      </li>
      <li>
        <svg viewBox="0 0 16 16" aria-hidden="true"><path d="M1 4h14v9H1z M1.5 4.5L8 9l6.5-4.5" stroke="#fff" stroke-width="1"/></svg>
        info@BrightwellDentalCareMi.com
      </li>
      <li>
        <svg viewBox="0 0 16 16" aria-hidden="true"><circle cx="8" cy="8" r="7"/><path d="M1 8h14M8 1c-3 3-3 11 0 14M8 1c3 3 3 11 0 14" stroke="#fff" stroke-width="1" fill="none"/></svg>
        BrigthwellDentalCareMi.com
      </li>
    </ul>

    <div class="address">2730 W. Halvert Rd. Ste. 7 Royal Oak, MI 48391</div>
  </section>

  <!-- Back of card -->
  <section class="card card-back" aria-label="Appointment card back">
    <h2 class="appt-title">YOUR APPOINTMENT</h2>
    <div class="brand">
      <span class="brand-dot"></span>
      <span class="brand-name"><span class="word">Brightwell</span><span class="sub">DENTAL CARE</span></span>
    </div>

    <span class="field label-name">Name :</span>
    <span class="dots dots-name"></span>
    <span class="field label-date">Date :</span>
    <span class="dots dots-date"></span>
    <span class="field label-time">Time :</span>
    <span class="dots dots-time"></span>
    <span class="field label-ampm">am / pm</span>

    <span class="field label-next">Next Appointment</span>
    <span class="slot slot-1"></span>
    <span class="slot slot-2"></span>
    <span class="slot slot-3"></span>

    <div class="days">
      <div class="days-week"></div>
      <div class="days-sat"></div>
      <span class="day" style="left:70px">MON</span><span class="day-box" style="left:140px;width:51px"></span>
      <span class="day" style="left:202px">TUE</span><span class="day-box" style="left:258px;width:51px"></span>
      <span class="day" style="left:320px">WED</span><span class="day-box" style="left:385px;width:51px"></span>
      <span class="day" style="left:447px">THU</span><span class="day-box" style="left:507px;width:51px"></span>
      <span class="day" style="left:569px">FRI</span><span class="day-box" style="left:617px;width:51px"></span>
      <span class="day" style="left:677px">SAT</span><span class="day-box" style="left:735px;width:52px"></span>
    </div>

    <p class="notice">If you are unable to keep your appointment, kindly give 48 hours notice</p>
  </section>

</div>
</body>
</html>
```